New web design for a service provider in the medical field

We are looking for a new design for our website. We are a company that repairs and sells medical endoscopes. Our customers include doctors and hospitals. Our current website can be found at https://lumavex.de/en/lumavex-english.
We need a new web design (without programming) for the following 3 pages:
-Startpage https://lumavex.de/en/lumavex-english/
-Used endoscopes https://lumavex.de/en/used-endoscopes/
-Purchase https://lumavex.de/en/purchase/
The design should be modern and stylish.
The blue color of the logo should be reflected on the page, but not too intrusive.
I have uploaded the images from the header. If more images are needed, let me know and I will upload them.

Target Market(s)
Doctors and hospitals

```html
<!DOCTYPE html>
<html lang="en">
<head>
<meta charset="utf-8">
<title>Lumavex – Endoscope Repair and Sales</title>
<link href="https://fonts.googleapis.com/css2?family=Poppins:wght@300;400;500;600;700;800&display=swap" rel="stylesheet">
<style>
:root{
  --blue:#0b57b0;
  --blue-dark:#0a4fa6;
  --sky:#1a9ee0;
  --ink:#222;
  --muted:#555;
  --pale:#eef4fa;
  --white:#fff;
}
*{box-sizing:border-box;margin:0;padding:0}
html,body{width:1200px;height:3877px;overflow:hidden}
body{font-family:"Poppins",sans-serif;color:var(--ink);background:var(--white);position:relative}
a{color:inherit;text-decoration:none}
.topbar{height:95px;display:flex;align-items:center;padding:0 110px;font-size:14px;color:#333}
.brand{display:flex;align-items:center;gap:8px;font-weight:700;font-size:18px;color:var(--blue);margin-right:36px}
.brand-dot{width:12px;height:12px;border-radius:50%;background:var(--sky)}
.toplinks{display:flex;gap:14px}
.contact{margin-left:auto;display:flex;gap:28px;align-items:center}
.contact span{display:flex;align-items:center;gap:6px}
.mainnav{height:44px;background:var(--blue);display:flex;padding-left:126px;font-size:14px;color:#fff}
.mainnav a{padding:0 26px;line-height:44px}
.mainnav a.active{background:var(--sky)}
.hero{position:relative;height:637px;overflow:hidden}
.hero-photo{position:absolute;inset:0;background:linear-gradient(120deg,#e6f1f5 0%,#bfdbe6 40%,#7fb7cf 70%,#2d5f7a 100%)}
.hero h1{position:absolute;left:108px;top:200px;color:#fff;font-weight:800;font-size:48px;line-height:82px}
.arrow{position:absolute;top:270px;color:#fff;font-size:34px}
.hero svg{position:absolute;bottom:0;left:0}
.service{background:var(--pale);height:255px;text-align:center;padding-top:20px}
.service .kicker{color:var(--blue);font-size:19px}
.service h2{font-size:40px;font-weight:700;margin:4px 0 20px}
.service p{font-size:13px;color:var(--muted);line-height:26px;width:720px;margin:0 auto}
.intro-title{text-align:center;color:var(--blue);font-weight:700;font-size:25px;line-height:41px;margin-top:78px}
.about{position:relative;height:420px}
.about-text{position:absolute;left:111px;top:70px;width:450px;font-size:13.5px;line-height:26.5px;color:#444}
.about-text p{margin-bottom:16px}
.frame-back{position:absolute;left:668px;top:14px;width:447px;height:337px;border:1px solid var(--sky)}
.frame-under{position:absolute;left:626px;top:50px;width:446px;height:337px;background:#dbe7f3}
.about-photo{position:absolute;left:643px;top:35px;width:446px;height:337px;background:linear-gradient(135deg,#f2f3f4,#c9ccd0 55%,#6e7176);box-shadow:0 6px 18px rgba(0,0,0,.2)}
.section-title{text-align:center;color:var(--blue);font-weight:700;font-size:42px;margin-top:18px}
.cards{display:flex;gap:25px;justify-content:center;margin-top:30px}
.card{width:301px;height:433px;background:#fff;box-shadow:0 3px 10px rgba(0,0,0,.15)}
.card-photo{height:225px}
.card-body{padding:20px 17px}
.card .tag{color:var(--blue);font-size:15px}
.card h3{font-size:15px;font-weight:500;margin:6px 0 10px}
.card p{font-size:12px;color:#555;line-height:23px;padding:0 3px;height:80px}
.card a{color:var(--blue);font-size:13.5px;text-decoration:underline;padding-left:7px}
.faulty{position:absolute;top:2292px;left:0;width:1200px;height:506px;background:linear-gradient(180deg,#3a3f47,#24282e);text-align:center;color:#fff}
.faulty h2{font-size:43px;font-weight:700;margin-top:150px}
.faulty p{font-size:15px}
.faulty .btn{display:inline-block;margin-top:26px;width:250px;line-height:54px;border-radius:27px;background:var(--sky);font-weight:600;font-size:15px}
.features{position:absolute;top:2862px;left:0;width:1200px;text-align:center}
.features h2{font-size:23px;font-weight:600}
.grid{display:grid;grid-template-columns:repeat(3,300px);column-gap:40px;justify-content:center;margin-top:30px;row-gap:40px}
.feat svg{height:70px}
.feat h3{font-size:15px;font-weight:500;margin:6px 0 6px}
.feat p{font-size:11.5px;color:#555;line-height:23px}
.footer{position:absolute;top:3380px;left:0;width:1200px;height:497px;color:#fff}
.footer svg.wave{position:absolute;top:0;left:0}
.footer-inner{position:absolute;top:200px;left:108px;width:980px}
.footer h2{font-size:41px;font-weight:800}
.footer .btn{position:absolute;right:0;top:-8px;width:250px;line-height:54px;border-radius:27px;background:var(--sky);text-align:center;font-weight:600;font-size:15px}
.footer hr{border:0;border-top:1px solid rgba(255,255,255,.6);margin-top:40px}
.footer nav{display:flex;justify-content:center;gap:37px;margin-top:44px;font-size:15.5px}
.social{display:flex;justify-content:center;gap:10px;margin-top:26px}
.social span{width:13px;height:13px;border-radius:50%;border:2px solid #fff}
.copy{text-align:center;font-size:13px;margin-top:22px}
</style>
</head>
<body>
<header class="topbar">
  <a class="brand" href="https://lumavex.de/en/lumavex-english/"><span class="brand-dot"></span>Lumavex</a>
  <nav class="toplinks"><a href="#">Pick-up order</a><a href="#">About us</a><a href="#">Contact us</a></nav>
  <div class="contact">
    <span><svg width="13" height="10" viewBox="0 0 13 10"><rect width="13" height="10" rx="1" fill="#1a9ee0"/><path d="M0 0l6.5 5L13 0" stroke="#fff" fill="none"/></svg>info@lumavex.de</span>
    <span><svg width="12" height="12" viewBox="0 0 12 12"><path d="M2 1l2 0 1 3-1.5 1a7 7 0 003.5 3.5L8 7l3 1v2a1 1 0 01-1 1A9 9 0 011 2a1 1 0 011-1z" fill="#1a9ee0"/></svg>+49 4100 555 120-0</span>
    <span>Eng ⌄</span>
  </div>
</header>
<nav class="mainnav">
  <a class="active" href="https://lumavex.de/en/lumavex-english/">Home</a><a href="#">Endoscope Repair</a><a href="https://lumavex.de/en/used-endoscopes/">Used Endoscopes</a><a href="#">Endoscopy Systems</a><a href="#">Endoscopy Accessories</a><a href="https://lumavex.de/en/purchase/">Purchase</a>
</nav>
<section class="hero">
  <div class="hero-photo" role="img" aria-label="Gloved hands of a clinician holding a flexible endoscope"></div>
  <h1>Put Your Endoscope<br>In Reliable Hands!</h1>
  <span class="arrow" style="left:42px">‹</span><span class="arrow" style="right:42px">›</span>
  <svg width="1200" height="160" viewBox="0 0 1200 160"><path d="M0 120C150 20 330 -10 560 60S960 170 1200 110V160H0Z" fill="#1a9ee0"/><path d="M0 135C170 40 350 20 580 80S980 170 1200 120V160H0Z" fill="#eef4fa"/></svg>
</section>
<section class="service">
  <div class="kicker">Your Future</div>
  <h2>Our Service</h2>
  <p>Lumavex GmbH is specialised in the repair and sale of Orvian, Pentara and Fujora flexible medical endoscopes. As a service-oriented company, we are at your side with our knowledge and skills!</p>
</section>
<h2 class="intro-title">Endoscope repairs and second hand endoscopes from<br>Lumavex – cause the outcome matters!</h2>
<section class="about">
  <div class="about-text">
    <p>Lumavex is a privileged partner for the start-up facility or optimisation of existing healthcare facilities, doctor's offices and hospitals. The quality and reliability of our products and our offered service are our best advertisement!</p>
    <p>As a result of optimised processes and highly qualified specialists in our company, we can work very quickly and with high quality for your benefit of least possible restrictions in your doctor's office or in your hospital.</p>
  </div>
  <div class="frame-back"></div>
  <div class="frame-under"></div>
  <div class="about-photo" role="img" aria-label="Close-up of an endoscope control body in a holder"></div>
</section>
<h2 class="section-title">Used Endoscopes</h2>
<div class="cards">
  <article class="card"><div class="card-photo" role="img" aria-label="Technician cleaning an endoscope in a basin" style="background:linear-gradient(135deg,#dfe6ee,#9fb2c8 60%,#2b3a52)"></div>
    <div class="card-body"><div class="tag">Repair</div><h3>Endoscope repair service</h3><p>Manufacturer-independent we repair and maintain endoscopes,components (e.g. processors or light sources),</p><a href="#">Repair request</a></div></article>
  <article class="card"><div class="card-photo" role="img" aria-label="Doctor in blue gloves holding an endoscope" style="background:linear-gradient(135deg,#eef0f3,#c8ced6 55%,#2c5fc6)"></div>
    <div class="card-body"><div class="tag">Sale</div><h3>Used endoscopes</h3><p>Our regular stock includes refurbished gastroscopes, coloscopes, bronchoscopes, cystoscopes and duodenoscopes</p><a href="https://lumavex.de/en/purchase/">Purchase request</a></div></article>
  <article class="card"><div class="card-photo" role="img" aria-label="Endoscopes laid out on a blue surgical cloth" style="background:linear-gradient(135deg,#b9cde6,#5d86c0 55%,#1d3b6e)"></div>
    <div class="card-body"><div class="tag">Purchase</div><h3>Used endoscopes</h3><p>We are very interested in buying your old endoscopes – even defective dismantled! We offer fair conditions! Please</p><a href="#">Sell device</a></div></article>
</div>
<section class="faulty" role="img" aria-label="Dim hospital ward with beds">
  <h2>Faulty Endoscope?</h2>
  <p>We ensure quick and smooth repairs!</p>
  <p style="font-weight:600">Simple place a</p>
  <a class="btn" href="#">Pick-up order</a>
</section>
<section class="features">
  <h2>Lumavex GmbH, your decision for your future</h2>
  <div class="grid">
    <div class="feat"><svg viewBox="0 0 70 70" width="70"><g stroke="#1a9ee0" stroke-width="3" fill="none"><path d="M12 58L44 26M20 14l36 36M50 10a10 10 0 00-10 14L12 52l6 6 28-28a10 10 0 0014-10l-6 6-6-2-2-6z"/></g></svg><h3>Fast repairs</h3><p>Keep potential disruptions in your doctor's office or in your hospital at minimum as a result of optimized processes and highly qualified specialists in our company</p></div>
    <div class="feat"><svg viewBox="0 0 70 70" width="70"><path d="M8 34L35 8l27 26M16 28v34h14V44h10v18h14V28" stroke="#1a9ee0" stroke-width="3" fill="none"/></svg><h3>On-site service</h3><p>We will gladly pay you a visit to to carry out analysis and repairs on site. Due to our many years of experience – it doesn't get any faster (whigleithin a 250 km range)</p></div>
    <div class="feat"><svg viewBox="0 0 70 70" width="70"><circle cx="35" cy="35" r="30" stroke="#1a9ee0" stroke-width="3" fill="none"/><path d="M22 36l9 9 17-18" stroke="#1a9ee0" stroke-width="3" fill="none"/></svg><h3>Without a maintenance contract</h3><p>No subscription or other maintenance contract, but one-time and sustainable repair work</p></div>
    <div class="feat"><svg viewBox="0 0 70 70" width="70"><path d="M27 8h16l-5 10h-6zM32 18c-14 8-20 22-18 34 2 10 40 10 42 0 2-12-4-26-18-34" stroke="#1a9ee0" stroke-width="3" fill="none"/><text x="35" y="52" text-anchor="middle" font-size="20" fill="#1a9ee0" font-family="Poppins,sans-serif">$</text></svg><h3>Highly cost efficient</h3><p>Benefit from our first class recommendations and implementation by our experienced staff. Our goals is to find the best solutions together with you at the best lowest price point.</p></div>
    <div class="feat"><svg viewBox="0 0 70 70" width="70"><path d="M12 36h10v26H12zM22 40l10-14 4 2-2 10h18a4 4 0 010 8h-2a4 4 0 010 8h-2a4 4 0 010 8H22M46 8l3 7 7 3-7 3-3 7-3-7-7-3 7-3z" stroke="#1a9ee0" stroke-width="3" fill="none"/></svg><h3>Loan equipment service</h3><p>Use our service of high-quality loan devices during the downtime of your defective endoscope (limited to stock)</p></div>
    <div class="feat"><svg viewBox="0 0 70 70" width="70"><circle cx="35" cy="28" r="20" stroke="#1a9ee0" stroke-width="3" fill="none"/><circle cx="35" cy="28" r="12" stroke="#1a9ee0" stroke-width="2" fill="none"/><path d="M22 44l-6 18 8-4 6 6 4-16M48 44l6 18-8-4-6 6-4-16" stroke="#1a9ee0" stroke-width="3" fill="none"/></svg><h3>First class service</h3><p>Our clients always come first!</p></div>
  </div>
</section>
<footer class="footer">
  <svg class="wave" width="1200" height="497" viewBox="0 0 1200 497"><path d="M0 20C250 140 500 150 760 80S1080 0 1200 20V497H0Z" fill="#1a9ee0"/><path d="M0 40C260 170 520 160 780 100S1090 40 1200 50V497H0Z" fill="#0b57b0"/></svg>
  <div class="footer-inner">
    <h2>How Can We Help You?</h2>
    <a class="btn" href="#">Send us a message</a>
    <hr>
    <nav><a href="#">Informations</a><a href="#">About Us</a><a href="#">Contact Us</a><a href="#">Tos</a><a href="#">Copyrights</a><a href="#">Privacy Policy</a></nav>
    <div class="social"><span></span><span></span></div>
    <p class="copy">© 2022 All Rights Reserved</p>
  </div>
</footer>
</body>
</html>
```